Business Card for Vorla Parts Wholesale supplier

Hi There! I need a new business card for our company. We are specialized in selling Vorla parts, mostly we sell new LCD screens for Zelnar and Drelks. I would like to see that back in the design.

You can find the colors and logo's on our website: www.hartuvo.nl

Industry/Entity Type

Business

Contact Information for Business Card

My Details:
Tobias Lindqvist

Phone: 0031687203316
E-mail: Tobias@hartuvo.nl

Slogan: "Because Quality Matters"

Font styles to use
Sans Serif

Colors

Designer to choose colors to be used in the design.

Requirements
Must have
• A Black backside with the Hartuvo logo on it. The front side should be clean with only my contact details.
• But I'm also open for something really different or awesome!
Nice to have
• Remember that we are in the parts & repairing industry, So i'll be handing those business cards mainly to repair companies. Maybe you can do something with that thought :)

```html
<!DOCTYPE html>
<html lang="en">
<head>
<meta charset="utf-8">
<title>Hartuvo Business Card</title>
<link rel="stylesheet" href="https://fonts.googleapis.com/css2?family=Open+Sans:wght@400;600;700;800&display=swap">
<style>
  :root {
    --page-bg: #e9e7e4;
    --card-black: #000000;
    --card-silver-light: #f4f4f4;
    --card-silver-dark: #cfd0d1;
    --brand-orange: #f07322;
    --text-dark: #111111;
    --text-light: #ffffff;
  }
  * { margin: 0; padding: 0; box-sizing: border-box; }
  html, body {
    width: 1200px;
    height: 900px;
    overflow: hidden;
    background: var(--page-bg);
    font-family: "Open Sans", Arial, sans-serif;
  }
  .business-card {
    position: absolute;
    left: 100px;
    top: 141px;
    width: 1000px;
    height: 618px;
    overflow: hidden;
    box-shadow: 0 12px 30px rgba(0,0,0,0.18);
  }
  .band-top {
    position: absolute;
    left: 0; top: 0;
    width: 100%; height: 187px;
    background: var(--card-black);
  }
  .band-middle {
    position: absolute;
    left: 0; top: 187px;
    width: 100%; height: 227px;
    background: linear-gradient(90deg, var(--card-silver-dark) 0%, var(--card-silver-light) 35%, var(--card-silver-light) 65%, var(--card-silver-dark) 100%);
  }
  .band-bottom {
    position: absolute;
    left: 0; top: 414px;
    width: 100%; height: 204px;
    background: var(--brand-orange);
  }
  .holder-name {
    position: absolute;
    right: 64px;
    top: 60px;
    color: var(--brand-orange);
    font-size: 38px;
    font-weight: 600;
    letter-spacing: 1px;
    text-transform: uppercase;
    line-height: 1;
  }
  .brand-lockup {
    position: absolute;
    left: 95px;
    top: 210px;
    height: 182px;
    display: flex;
    align-items: center;
    gap: 60px;
  }
  .brand-square {
    width: 170px;
    height: 170px;
    background: var(--brand-orange);
  }
  .brand-name {
    color: var(--text-dark);
    font-size: 128px;
    font-weight: 800;
    line-height: 1;
    letter-spacing: -2px;
  }
  .contact-block {
    position: absolute;
    right: 64px;
    top: 440px;
    text-align: right;
    color: var(--text-light);
    font-size: 24px;
    line-height: 37px;
  }
  .contact-label { font-weight: 700; }
  .contact-row span + span { margin-left: 30px; }
  .slogan {
    position: absolute;
    right: 64px;
    top: 540px;
    color: var(--text-light);
    font-size: 29px;
    font-weight: 600;
    letter-spacing: 0.5px;
    text-transform: uppercase;
    line-height: 1;
  }
</style>
</head>
<body>
  <div class="business-card">
    <div class="band-top"></div>
    <div class="band-middle"></div>
    <div class="band-bottom"></div>

    <p class="holder-name">Tobias Lindqvist</p>

    <div class="brand-lockup">
      <div class="brand-square"></div>
      <span class="brand-name">hartuvo</span>
    </div>

    <div class="contact-block">
      <p class="contact-row"><span><span class="contact-label">P:</span> 0031687203316</span></p>
      <p class="contact-row"><span><span class="contact-label">E:</span> Tobias@hartuvo.nl</span><span>www.hartuvo.nl</span></p>
    </div>

    <p class="slogan">Because Quality Matters</p>
  </div>
</body>
</html>
```